Business Card and Letterhead for Pimlu - modern real estate business

I need a double sided business card design for Pimlu. Please see business card brief here https://files.trelvonadocs.com/sheet/r/7QzTmWbaXLJnoPEd-kRyUgFhHsstbvCe2qfoMxDa_pz/view?mode=shared

Please feel free to design the business cards however you feel best. I am happy to give some creative freedoms and then provide feedback from there.

Please then also create a letterhead to match the business card design

Colors

Designer to choose colors to be used in the design.

Requirements
Must have
• Must be a modern, elegant business card which looks very professional

```html
<!DOCTYPE html>
<html lang="en">
<head>
<meta charset="utf-8">
<title>Pimlu – Business Card and Letterhead</title>
<link href="https://fonts.googleapis.com/css2?family=Lato:wght@400;700;900&display=swap" rel="stylesheet">
<style>
  :root {
    --backdrop: #ece8e3;
    --paper: #ffffff;
    --ink: #1a1a1a;
    --card: #151515;
    --red: #e3212b;
    --white: #f2f2f2;
  }
  * { box-sizing: border-box; margin: 0; padding: 0; }
  html, body { width: 1200px; height: 900px; overflow: hidden; }
  body {
    position: relative;
    background: var(--backdrop);
    font-family: 'Lato', sans-serif;
    color: var(--ink);
  }

  /* Letterhead */
  .letterhead {
    position: absolute; left: 132px; top: 112px;
    width: 493px; height: 698px;
    background: var(--paper);
  }
  .letterhead__brand {
    position: absolute; left: 36px; top: 24px;
    font-weight: 900; font-size: 38px; letter-spacing: 3px;
    color: var(--red); line-height: 1;
  }
  .letter {
    position: absolute; left: 47px; top: 177px; width: 401px;
    font-size: 9.4px; line-height: 12px; text-align: justify;
  }
  .letter__greeting { margin-bottom: 17px; }
  .letter p { margin-bottom: 24px; }
  .letter__signoff { text-align: left; line-height: 13px; margin-top: -6px; }
  .letterhead__rule {
    position: absolute; left: 0; right: 0; top: 659px; height: 3px;
    background: var(--red);
  }
  .letterhead__footer {
    position: absolute; left: 0; right: 0; top: 665px; height: 33px;
    background: var(--ink); color: var(--white);
    font-size: 10px; display: flex; align-items: center; justify-content: center;
    gap: 6px; white-space: nowrap;
  }

  /* Business cards */
  .card {
    position: absolute; left: 713px; width: 408px; height: 247px;
    background: var(--card); color: var(--white);
  }
  .card::after {
    content: ""; position: absolute; left: 0; right: 0; bottom: 0; height: 2px;
    background: var(--red);
  }
  .card--front { top: 169px; }
  .card--back { top: 461px; }

  .card__portrait { position: absolute; left: 34px; top: 50px; width: 146px; height: 146px; }
  .card__divider {
    position: absolute; left: 205px; top: 53px; width: 1px; height: 140px;
    background: var(--red);
  }
  .card__details { position: absolute; left: 227px; top: 55px; }
  .card__name { font-weight: 700; font-size: 19px; color: var(--red); line-height: 22px; }
  .card__role { font-size: 11px; line-height: 14px; margin-top: 3px; }
  .card__address { font-size: 11px; line-height: 13px; margin-top: 13px; }
  .card__contacts { list-style: none; margin-top: 11px; font-size: 11px; }
  .card__contacts li { display: flex; align-items: center; gap: 8px; height: 15.5px; }
  .card__contacts svg { width: 11px; height: 11px; flex: none; }

  .card__brand {
    position: absolute; left: 0; right: 0; top: 92px;
    text-align: center; font-weight: 900; font-size: 68px; letter-spacing: 6px;
    color: var(--red); line-height: 1;
  }
</style>
</head>
<body>

<section class="letterhead">
  <div class="letterhead__brand">PIMLU</div>
  <div class="letter">
    <div class="letter__greeting">Dear Sir/Mam,</div>
    <p>Contrary to popular belief, Lorem Ipsum is not simply random text. It has roots in a piece of classical Latin literature from 45 BC, making it over 2000 years old. Edwin Marlow, a Latin professor at Ashford Crane College in Vermont, looked up one of the more obscure Latin words, consectetur, from a Lorem Ipsum passage, and going through the cites of the word in classical literature, discovered the undoubtable source.</p>
    <p>Lorem Ipsum comes from sections 1.10.32 and 1.10.33 of "de Finibus Bonorum et Malorum" (The Extremes of Good and Evil) by Calvius, written in 45 BC. This book is a treatise on the theory of ethics, very popular during the Renaissance. The first line of Lorem Ipsum, "Lorem ipsum dolor sit amet..", comes from a line in section 1.10.32.</p>
    <p>The standard chunk of Lorem Ipsum used since the 1500s is reproduced below for those interested. Sections 1.10.32 and 1.10.33 from "de Finibus Bonorum et Malorum" by Calvius are also reproduced in their exact original form, accompanied by English versions from the 1914 translation by H. Dellow.</p>
    <p>The standard chunk of Lorem Ipsum used since the 1500s is reproduced below for those interested.</p>
    <div class="letter__signoff">Best Regards<br>Jonah Reid<br>Licenced Real Estate Agent</div>
  </div>
  <div class="letterhead__rule"></div>
  <div class="letterhead__footer">
    <span>0400 118 392</span><span>|</span><span>jonah@pimlu.com</span><span>|</span><span>www.pimlu.com</span><span>|</span><span>PO Box 1180. Larkvale NSW 2790</span>
  </div>
</section>

<section class="card card--front">
  <svg class="card__portrait" viewBox="0 0 146 146" role="img" aria-label="Portrait photo of the agent outdoors">
    <defs>
      <linearGradient id="portraitTone" x1="0" y1="0" x2="0" y2="1">
        <stop offset="0" stop-color="#b9c3c6"/>
        <stop offset="0.5" stop-color="#7c8a6a"/>
        <stop offset="1" stop-color="#2c2e2e"/>
      </linearGradient>
    </defs>
    <circle cx="73" cy="73" r="71" fill="url(#portraitTone)" stroke="var(--red)" stroke-width="2"/>
  </svg>
  <div class="card__divider"></div>
  <div class="card__details">
    <div class="card__name">Jonah Reid</div>
    <div class="card__role">Licenced Real Estate Agent</div>
    <div class="card__address">PO Box 1180<br>Larkvale NSW 2790</div>
    <ul class="card__contacts">
      <li>
        <svg viewBox="0 0 24 24"><path fill="var(--red)" d="M6.6 10.8c1.4 2.8 3.8 5.1 6.6 6.6l2.2-2.2c.3-.3.7-.4 1-.2 1.1.4 2.3.6 3.6.6.6 0 1 .4 1 1V20c0 .6-.4 1-1 1C10.6 21 3 13.4 3 4c0-.6.4-1 1-1h3.5c.6 0 1 .4 1 1 0 1.3.2 2.5.6 3.6.1.3 0 .7-.2 1z"/></svg>
        <span>0400 118 392</span>
      </li>
      <li>
        <svg viewBox="0 0 24 24"><rect x="2" y="5" width="20" height="14" fill="var(--red)"/><path d="M2 5l10 8 10-8" fill="none" stroke="var(--card)" stroke-width="2"/></svg>
        <span>jonah@pimlu.com</span>
      </li>
      <li>
        <svg viewBox="0 0 24 24" fill="none" stroke="var(--red)" stroke-width="2"><circle cx="12" cy="12" r="10"/><ellipse cx="12" cy="12" rx="4" ry="10"/><path d="M2 12h20"/></svg>
        <span>www.pimlu.com</span>
      </li>
    </ul>
  </div>
</section>

<section class="card card--back">
  <div class="card__brand">PIMLU</div>
</section>

</body>
</html>
```